Personal Training Business at home (Fern Vitality & Health)

My business name will be Fern Vitality & Health and will be training people with special needs (Asthma, Diabetes, Obesity, Rehab, Sports Performance) for all ages. It will be set indoor and outdoor for all types of weather conditions. I,m also doing Pilates group classes as well in a Japanese garden setting.I will be working alone so the groups will be small and the client has a high quality of service. I just need something very basic to start with then as the business expands I can edit it to it,s growth.

Target Market(s)

Target special population persons with dysfunctions injuries, metabolic/cardio-respiratory conditions, sports performance and more also healthy food choices.

Industry/Entity Type

Business

Number of Pages Required

3 page

Font styles to use
Serif

Colors
f78f20
ffffff
474747
cbcbcb
abd036

Requirements
Must have
• The website must have accessibility for change, to be able to link on other networks like my own YouTube videos. A basic lay out so I can fill in the pages and ad more as I expand the business. The logo to have the A for Fern to be an image of a man shaped as the letter A with his arms extended out/up. Private Facility and must ring for appointment to enter premises.
Nice to have
• The Image I want to have in my studio is for people to be serious about training & health choices. I want them to be able to train in a comfortable environment and free of air conditioned concrete rooms with machines. My home is converted to a Organic feature and outdoor/indoor training facility that my clients & I can share the natural freedom of training in the elements. My client have special needs and need extra care, they are people with injuries, metabolic/cardio-respiratory condition, asthmatics & more they need to be screened and tested for the condition that they suffer from and together with there allied professional we work together to treat them with the up most care for maximum results. This is what I want to target I long term client with real Goals on there mind and not some pipe dream.
Should not have
• Not to be portray as a Gym with machines and clients that only care about image.

```html
<!DOCTYPE html>
<html lang="en">
<head>
<meta charset="utf-8">
<title>Fern Fitness — Why train with us</title>
<link href="https://fonts.googleapis.com/css2?family=Open+Sans:wght@400;600;700;800&family=Roboto:wght@400;500&display=swap" rel="stylesheet">
<style>
:root{
  --green:#abd036;
  --orange:#f78f20;
  --ink:#474747;
  --line:#cbcbcb;
  --white:#ffffff;
}
*{margin:0;padding:0;box-sizing:border-box}
html,body{width:1200px;height:1073px;overflow:hidden;background:var(--white)}
.page{position:relative;width:1200px;height:1073px;font-family:'Open Sans',Arial,sans-serif;color:var(--ink)}
.abs{position:absolute}

/* header */
.site-header{position:absolute;left:0;top:0;width:1200px;height:106px;background:var(--green)}
.brand{position:absolute;left:159px;top:38px;font-family:'Open Sans',sans-serif;font-weight:800;font-size:34px;color:var(--white);letter-spacing:-0.5px;display:flex;align-items:center;gap:10px}
.brand-dot{width:14px;height:14px;border-radius:50%;background:var(--white)}
.contact-block{position:absolute;color:var(--white)}
.contact-label{font-size:11.5px;font-weight:700;letter-spacing:2px;text-transform:uppercase}
.contact-value{display:flex;align-items:center;gap:8px;font-weight:700}
.contact-email{left:668px;top:39px}
.contact-email .contact-label{margin-left:21px}
.contact-email .contact-value{font-size:14px;margin-top:1px}
.contact-divider{left:887px;top:40px;width:1px;height:32px;background:#c7e07a}
.contact-phone{left:914px;top:35px}
.contact-phone .contact-label{margin-left:23px}
.contact-phone .contact-value{font-size:18.5px;margin-top:0}

/* nav */
.main-nav{position:absolute;left:0;top:106px;width:1200px;height:32px;background:var(--orange)}
.main-nav a{position:absolute;top:0;height:32px;line-height:32px;color:var(--white);font-size:11.8px;font-weight:600;text-decoration:none;white-space:nowrap}
.main-nav .active{background:var(--green);padding:0 13px;left:392px;width:128px}
.nav-sep{position:absolute;top:9px;width:1px;height:16px;background:#fbc287}

/* hero */
.hero{position:absolute;left:0;top:138px;width:1200px;height:328px;
  background:
   radial-gradient(ellipse at 30% 30%,rgba(120,150,80,.75),transparent 55%),
   radial-gradient(ellipse at 80% 25%,rgba(100,130,70,.7),transparent 50%),
   radial-gradient(ellipse at 70% 85%,rgba(200,110,90,.55),transparent 45%),
   linear-gradient(180deg,#5c6147 0%,#6a6455 45%,#8a7e70 100%)}
.hero-title{position:absolute;left:0;top:345px;width:1200px;text-align:center;color:var(--white);font-weight:700;font-size:25px;line-height:30px;letter-spacing:.2px;text-shadow:0 1px 3px rgba(0,0,0,.5)}
.hero-dots{position:absolute;top:425px;left:0;width:1200px;height:12px}
.hero-dots span{position:absolute;width:8px;height:8px;border-radius:50%;background:var(--white);top:2px}
.hero-dots .current{width:12px;height:12px;top:0;background:transparent;border:2px solid var(--white)}

/* intro */
.section-title{left:162px;top:506px;font-family:'Roboto',sans-serif;font-weight:400;font-size:22px;color:var(--orange)}
.intro-text{left:162px;top:549px;width:880px;font-family:'Roboto',sans-serif;font-size:12.6px;line-height:24px;color:var(--ink)}
.client-icons{left:0;top:0}
.client-icon{position:absolute;width:88px;height:88px;border-radius:50%;border:2px solid #e3e3e3;top:656px;background:var(--white)}
.client-icon span{position:absolute;left:24px;top:24px;width:36px;height:36px;border-radius:50%;background:#8e8e8e}

/* footer */
.site-footer{position:absolute;left:0;top:803px;width:1200px;height:270px;background:var(--green)}
.footer-heading{position:absolute;top:32px;font-size:11.5px;font-weight:700;color:var(--ink);text-transform:uppercase}
.field{position:absolute;background:var(--white);font-family:'Roboto',sans-serif;font-size:11.5px;color:#666;display:flex;align-items:center;gap:7px;padding-left:11px}
.field.tall{align-items:flex-start;padding-top:11px}
.btn{position:absolute;background:var(--orange);color:var(--white);font-weight:800;letter-spacing:1.5px;text-align:center}
.footer-menu{position:absolute;left:420px;top:61px;list-style:none}
.footer-menu li{font-size:11px;line-height:18.8px;color:var(--ink)}
.social{position:absolute;left:637px;display:flex;align-items:center;gap:13px;font-family:'Roboto',sans-serif;font-size:11px;color:var(--ink)}
.social i{display:block;width:38px;height:38px;border-radius:50%}
.footer-brand{position:absolute;left:868px;top:185px;font-weight:800;font-size:32px;color:var(--white);letter-spacing:-0.5px}
.copyright{position:absolute;left:866px;top:236px;font-size:9.5px;color:var(--ink)}
</style>
</head>
<body>
<div class="page">

  <header class="site-header">
    <div class="brand"><span class="brand-dot"></span>Fern Fitness</div>

    <div class="contact-block contact-email">
      <div class="contact-label">E mail us</div>
      <div class="contact-value">
        <svg width="12" height="10" viewBox="0 0 12 10"><rect x="0" y="0" width="12" height="10" rx="1" fill="#fff"/><path d="M0 1 L6 6 L12 1" stroke="#abd036" stroke-width="1.4" fill="none"/></svg>
        hello@fernvitality.com
      </div>
    </div>
    <div class="abs contact-divider"></div>
    <div class="contact-block contact-phone">
      <div class="contact-label">Call us on</div>
      <div class="contact-value">
        <svg width="10" height="15" viewBox="0 0 10 15"><rect x="1" y="0.8" width="8" height="13.4" rx="1.5" fill="none" stroke="#fff" stroke-width="1.6"/><circle cx="5" cy="11.5" r="1" fill="#fff"/></svg>
        0491570156
      </div>
    </div>
  </header>

  <nav class="main-nav">
    <a style="left:165px">Home</a>
    <span class="nav-sep" style="left:211px"></span>
    <a style="left:228px">About FERN FIT &amp; HEALTH</a>
    <a class="active">Why train with us</a>
    <a style="left:539px">Training services</a>
    <span class="nav-sep" style="left:649px"></span>
    <a style="left:666px">Location</a>
    <span class="nav-sep" style="left:736px"></span>
    <a style="left:753px">Pricing &amp; packages</a>
    <span class="nav-sep" style="left:876px"></span>
    <a style="left:891px">Facilities</a>
    <span class="nav-sep" style="left:958px"></span>
    <a style="left:979px">Contact Us</a>
  </nav>

  <div class="hero" role="img" aria-label="Photo of a Japanese garden with bonsai trees on wooden stands and stone ground"></div>
  <h1 class="hero-title">ALL THESE PEOPLE ARE ALL ELIGIBLE<br>FOR THIS TYPE OF TRAINING</h1>
  <div class="hero-dots">
    <span style="left:542px"></span>
    <span class="current" style="left:566px"></span>
    <span style="left:595px"></span>
    <span style="left:622px"></span>
    <span style="left:650px"></span>
  </div>

  <h2 class="abs section-title">Why train with us</h2>
  <p class="abs intro-text">Our training services covers a wide variety of clients from different walks of life, like builders, plumbers, electricians, mechanics, truck drivers to your everyday common office workers, teachers, taxi drivers, nurses &amp; doctors and more. All these people are all eligible for this type of training. It is a great way to restore functional movement to deal with the everyday demands of your body &amp; just general fitness, health &amp; wellbeing.</p>

  <div class="abs client-icons">
    <div class="client-icon" style="left:159px" role="img" aria-label="Icon of builders"><span></span></div>
    <div class="client-icon" style="left:265px" role="img" aria-label="Icon of an office worker"><span></span></div>
    <div class="client-icon" style="left:372px" role="img" aria-label="Icon of a driver"><span></span></div>
    <div class="client-icon" style="left:476px" role="img" aria-label="Icon of a nurse"><span></span></div>
    <div class="client-icon" style="left:581px" role="img" aria-label="Icon of a mechanic"><span></span></div>
    <div class="client-icon" style="left:689px" role="img" aria-label="Icon of an electrician"><span></span></div>
    <div class="client-icon" style="left:794px" role="img" aria-label="Icon of an engineer"><span></span></div>
    <div class="client-icon" style="left:907px" role="img" aria-label="Icon of a doctor"><span></span></div>
  </div>

  <footer class="site-footer">
    <h3 class="footer-heading" style="left:161px">Quick Contact</h3>
    <div class="field" style="left:162px;top:62px;width:164px;height:35px">
      <svg width="9" height="10" viewBox="0 0 9 10"><circle cx="4.5" cy="3" r="2.5" fill="#999"/><path d="M0 10 Q4.5 4 9 10Z" fill="#999"/></svg>Name</div>
    <div class="field" style="left:162px;top:102px;width:164px;height:34px">
      <svg width="10" height="8" viewBox="0 0 10 8"><rect width="10" height="8" rx="1" fill="#999"/><path d="M0 1 L5 5 L10 1" stroke="#fff" fill="none"/></svg>E mail</div>
    <div class="field tall" style="left:162px;top:142px;width:164px;height:65px">
      <svg width="10" height="10" viewBox="0 0 10 10"><rect x="0.5" y="1.5" width="8" height="8" fill="none" stroke="#999"/><path d="M4 6 L9 1" stroke="#999" stroke-width="1.5"/></svg>Message</div>
    <div class="btn" style="left:243px;top:219px;width:83px;height:26px;line-height:26px;font-size:12px">SUBMIT</div>

    <h3 class="footer-heading" style="left:420px">Menu</h3>
    <ul class="footer-menu">
      <li>Home</li>
      <li>About FERN FIT &amp; HEALTH</li>
      <li>Why train with us</li>
      <li>Training services</li>
      <li>Our Location</li>
      <li>Trading hours</li>
      <li>Pricing &amp; packages</li>
      <li>Facilities</li>
      <li>Contact Us</li>
    </ul>

    <h3 class="footer-heading" style="left:637px">Follow us on</h3>
    <div class="social" style="top:58px"><i style="background:#2f4f8f"></i>Friendbook</div>
    <div class="social" style="top:105px"><i style="background:#1ea9e1"></i>Chirper</div>
    <div class="social" style="top:153px"><i style="background:#f05a28"></i>RSS Feed</div>

    <h3 class="footer-heading" style="left:849px">Newsletter Signup!</h3>
    <div class="field" style="left:850px;top:64px;width:166px;height:35px;color:#474747">
      <svg width="9" height="10" viewBox="0 0 9 10"><circle cx="4.5" cy="3" r="2.5" fill="#999"/><path d="M0 10 Q4.5 4 9 10Z" fill="#999"/></svg>Name</div>
    <div class="btn" style="left:850px;top:110px;width:166px;height:36px;line-height:36px;font-size:13px">SIGNUP!</div>

    <div class="footer-brand">Fern Fitness</div>
    <div class="copyright">Copyrights @ 2016 All Rights Reserved</div>
  </footer>

</div>
</body>
</html>
```